Design the Business card for NetVaultic

Business card required for a professional Cyber Security business.
Company Logo and Icon has already been provided however I would like other options for the logo and icon to compare to. Alternatively, please refine/enhance the image of the logo.icon I have already provided.

If you are going to use the provided logo and icon, I was thinking that the company raised Logo on White background would serve well on the front of the card. See attached. AND, a large company raised stand-alone icon to appear on black background on the back of the card with tagline 'Cyber Risk Management, Governance and Consulting' or 'Cyber Security for your Business' See attached.
Alternatively, provide your own design for the logo and icon.

Target Market(s)

Enterprise, Government, Financial.

Contact Information for Business Card

Tavin Orloweth
Founder and CEO

Email Address
Mobile Number
Website URL
LinkedIn URL

Logo Text

NetVaultic - see attached example of logo

Font styles to use
Other font styles liked:
• Berlin Sans FB

Requirements
Must have
• Clean large and bold icon on the back with tagline.
• Horizontal alignment,
Nice to have
• Round edges.
• Raised Logo/Icon
Should not have
• An unprofessional look and feel.

```html
<!DOCTYPE html>
<html lang="en">
<head>
<meta charset="utf-8">
<title>NetVaultic Business Card</title>
<link rel="stylesheet" href="https://fonts.googleapis.com/css2?family=Roboto:wght@400&family=Roboto+Condensed:wght@400;500&family=Varela+Round&display=swap">
<style>
  :root {
    --backdrop: #e9e6e1;
    --card: #1b1c1e;
    --ink: #ffffff;
    --divider: #5a5b5e;
    --brand-blue: #1f74c9;
    --tag-blue: #4a70c6;
    --tag-gold: #f2b705;
  }
  * { margin: 0; padding: 0; box-sizing: border-box; }
  html, body { width: 1200px; height: 960px; overflow: hidden; }
  body { background: var(--backdrop); position: relative; }

  .card {
    position: absolute;
    width: 600px;
    height: 342px;
    background: var(--card);
    box-shadow: 0 3px 8px rgba(0,0,0,0.25);
  }
  .card--front { left: 314px; top: 113px; }
  .card--back  { left: 311px; top: 472px; }

  .identity {
    position: absolute;
    right: 320px;
    top: 142px;
    text-align: right;
    color: var(--ink);
    font-family: "Roboto Condensed", sans-serif;
  }
  .identity__name { font-size: 24px; font-weight: 500; line-height: 28px; letter-spacing: 0.2px; }
  .identity__role { font-size: 17px; font-weight: 400; line-height: 24px; margin-top: 2px; }

  .divider {
    position: absolute;
    left: 313px;
    top: 117px;
    width: 1px;
    height: 103px;
    background: var(--divider);
  }

  .contacts {
    position: absolute;
    left: 343px;
    top: 131px;
    list-style: none;
    color: var(--ink);
    font-family: "Roboto", sans-serif;
    font-size: 14.5px;
  }
  .contacts li { display: flex; align-items: center; height: 19px; }
  .contacts svg { width: 12px; height: 12px; margin-right: 10px; fill: var(--ink); }

  .brand {
    position: absolute;
    left: 0; right: 0;
    top: 118px;
    display: flex;
    justify-content: center;
    align-items: center;
    gap: 16px;
  }
  .brand__dot { width: 40px; height: 40px; border-radius: 50%; background: var(--brand-blue); }
  .brand__name {
    font-family: "Varela Round", sans-serif;
    font-size: 46px;
    color: var(--brand-blue);
    line-height: 1;
  }

  .tagline {
    position: absolute;
    left: 0; right: 0;
    top: 276px;
    text-align: center;
    font-family: "Varela Round", sans-serif;
    font-size: 17.5px;
    color: var(--tag-blue);
  }
  .tagline__accent { color: var(--tag-gold); }
</style>
</head>
<body>
  <section class="card card--front">
    <div class="identity">
      <p class="identity__name">TAVIN ORLOWETH</p>
      <p class="identity__role">FOUNDER &amp; CEO</p>
    </div>
    <div class="divider"></div>
    <ul class="contacts">
      <li><svg viewBox="0 0 12 12"><path d="M3 0h6a1 1 0 0 1 1 1v10a1 1 0 0 1-1 1H3a1 1 0 0 1-1-1V1a1 1 0 0 1 1-1zm0 1.5v8h6v-8z"/></svg>555 204 7316</li>
      <li><svg viewBox="0 0 12 12"><path d="M0 2h12v1.2L6 7 0 3.2zM0 4.6l6 3.8 6-3.8V10H0z"/></svg>tavin@netvaultic.com</li>
      <li><svg viewBox="0 0 12 12"><circle cx="6" cy="6" r="5.5"/></svg>www.netvaultic.com</li>
      <li><svg viewBox="0 0 12 12"><circle cx="6" cy="6" r="5.5"/></svg>netvaultic</li>
    </ul>
  </section>

  <section class="card card--back">
    <div class="brand">
      <span class="brand__dot"></span>
      <span class="brand__name">NetVaultic</span>
    </div>
    <p class="tagline">Cyber Risk Management, <span class="tagline__accent">Governance &amp; Consulting</span></p>
  </section>
</body>
</html>
```